BrindleStaffing Business Card Design

We are a staffing company finding positions for dedicated nurses and physicians.

Target Market(s)

Business Professionals

Industry/Entity Type

Staffing

Contact Information for Business Card

Gordon Pratley
Chairman
417 39th Avenue South
SAINT PETERSBURG FL 33712
813-555-4172 Mobile
813-555-8036 Fax
gpratley@brindlestaffing.com
www.brindlestaffing.com

Font styles to use
Sans Serif

Colors
fbee3e
f04a50
f37122

Requirements
Must have
• Logo Attached, see colors below. We'd like to see Yellow, Orange and Red.

```html
<!DOCTYPE html>
<html lang="en">
<head>
<meta charset="utf-8">
<title>BrindleStaffing Business Card</title>
<link rel="stylesheet" href="https://fonts.googleapis.com/css2?family=Rubik:wght@400;500;600&display=swap">
<style>
  :root {
    --red: #f04a50;
    --orange: #f37122;
    --yellow: #fbee3e;
    --ink: #1f2430;
    --rule: #2e3a4e;
    --paper: #ffffff;
    --stage: #e6e7ea;
  }
  * { margin: 0; padding: 0; box-sizing: border-box; }
  html, body {
    width: 1200px; height: 1000px; overflow: hidden;
    background: var(--stage);
    font-family: "Rubik", Arial, sans-serif;
  }
  .card {
    position: absolute; left: 250px; width: 700px; height: 400px;
    border-radius: 4px; overflow: hidden;
    box-shadow: 0 6px 18px rgba(0,0,0,.18);
  }
  .card--front {
    top: 70px;
    background: linear-gradient(90deg, var(--red) 0%, var(--orange) 100%);
  }
  .card--back { top: 530px; background: var(--paper); }

  .brand {
    position: absolute; display: flex; align-items: center; gap: 10px;
    font-weight: 600; letter-spacing: -0.5px;
  }
  .brand__dot { width: 12px; height: 12px; border-radius: 50%; }
  .card--front .brand { right: 56px; top: 196px; font-size: 46px; color: var(--paper); }
  .card--front .brand__dot { background: var(--paper); }
  .card--back .brand { right: 40px; top: 52px; font-size: 44px; color: var(--orange); }
  .card--back .brand__dot { background: var(--orange); }

  .band { position: absolute; left: 0; top: 0; }

  .top-rule {
    position: absolute; left: 270px; top: 208px; width: 395px; height: 1px;
    background: var(--rule);
  }
  .person { position: absolute; left: 40px; top: 216px; display: flex; align-items: baseline; gap: 12px; }
  .person__name { font-size: 25px; font-weight: 600; color: var(--orange); }
  .person__title { font-size: 15px; color: var(--ink); }
  .person-rule {
    position: absolute; left: 40px; top: 250px; width: 385px; height: 1px;
    background: var(--rule);
  }
  .address { position: absolute; left: 40px; top: 258px; font-size: 15px; line-height: 20px; color: var(--ink); }
  .web {
    position: absolute; left: 40px; top: 304px; font-size: 15px; color: var(--ink);
    display: flex; align-items: center; gap: 6px;
  }
  .web__domain { color: var(--red); font-weight: 500; }

  .contact {
    position: absolute; right: 34px; top: 218px; text-align: right;
    font-size: 15px; line-height: 25px; color: var(--ink);
  }
  .contact__row { display: flex; justify-content: flex-end; align-items: center; gap: 8px; }
  .icon { width: 13px; height: 13px; flex: none; }
</style>
</head>
<body>

<section class="card card--front" aria-label="Card front">
  <div class="brand"><span>BrindleStaffing</span><span class="brand__dot"></span></div>
</section>

<section class="card card--back" aria-label="Card back">
  <svg class="band" width="700" height="400" viewBox="0 0 700 400" aria-hidden="true">
    <path d="M0,352 L430,352 C462,352 462,300 500,300 L700,300 L700,400 L0,400 Z" fill="var(--red)"/>
    <path d="M0,336 L420,336 C440,336 444,318 452,310 L458,318 C450,330 444,344 420,344 L0,344 Z" fill="var(--orange)"/>
  </svg>

  <div class="brand"><span>BrindleStaffing</span><span class="brand__dot"></span></div>

  <div class="top-rule"></div>

  <div class="person">
    <span class="person__name">Gordon Pratley</span>
    <span class="person__title">Chairman</span>
  </div>
  <div class="person-rule"></div>
  <div class="address">417 39th Avenue South<br>SAINT PETERSBURG FL 33712</div>
  <div class="web">
    <svg class="icon" viewBox="0 0 14 14" aria-hidden="true">
      <circle cx="7" cy="7" r="6" fill="none" stroke="var(--orange)" stroke-width="1.4"/>
      <ellipse cx="7" cy="7" rx="2.6" ry="6" fill="none" stroke="var(--orange)" stroke-width="1.1"/>
      <line x1="1" y1="7" x2="13" y2="7" stroke="var(--orange)" stroke-width="1.1"/>
    </svg>
    <span>www.<span class="web__domain">brindlestaffing</span>.com</span>
  </div>

  <div class="contact">
    <div class="contact__row">
      <span>813-555-4172</span>
      <svg class="icon" viewBox="0 0 14 14" aria-hidden="true">
        <path d="M3 1.5 L5.2 1.5 L6 4.5 L4.6 5.6 C5.4 7.4 6.6 8.6 8.4 9.4 L9.5 8 L12.5 8.8 L12.5 11 C12.5 12 11.8 12.5 11 12.5 C5.8 12.2 1.8 8.2 1.5 3 C1.5 2.2 2 1.5 3 1.5 Z" fill="var(--orange)"/>
      </svg>
    </div>
    <div class="contact__row">
      <span>813-555-8036</span>
      <svg class="icon" viewBox="0 0 14 14" aria-hidden="true">
        <rect x="3.5" y="1" width="7" height="4" fill="var(--orange)"/>
        <rect x="1" y="5.5" width="12" height="5" rx="1" fill="var(--orange)"/>
        <rect x="3.5" y="9" width="7" height="4" fill="var(--orange)" stroke="#fff" stroke-width="1"/>
      </svg>
    </div>
    <div class="contact__row">
      <span>gpratley@brindlestaffing.com</span>
      <svg class="icon" viewBox="0 0 14 14" aria-hidden="true">
        <rect x="1" y="3" width="12" height="8.5" rx="1" fill="var(--orange)"/>
        <path d="M1.5 3.5 L7 8 L12.5 3.5" fill="none" stroke="#fff" stroke-width="1.2"/>
      </svg>
    </div>
  </div>
</section>

</body>
</html>
```